Dorwin's Coating & Renewal Letterhead Design We want to revamp out old traditional letterhead with the new logo designs that are attached. We are working on getting all our company items from vehicles, business, cards, t-shirts, letterhead to match. This should include company colors, fonts, and flow of items that we have attached below.

Industry/Entity Type

Construction Company

Font styles to use
Sans Serif
Other font styles liked:
• Bold with outline

Colors
ec1f27
ffffff

Requirements
Must have
• Company Name: Dorwin's Coating & Renewal
• Address: 4728 SW 81st Ter Halverd cove fl 39417
• Office Number: (555) 413-2986
• Email: Dorwinrenewal@mailbrook.example
• License Number: KRT8046392
Nice to have
• Company Colors: red, white, black, and grey

```html
<!DOCTYPE html>
<html lang="en">
<head>
<meta charset="utf-8">
<title>Dorwin's Coating &amp; Renewal – Letterhead</title>
<link href="https://fonts.googleapis.com/css2?family=Montserrat:wght@400;600;700;800&display=swap" rel="stylesheet">
<style>
  :root {
    --brand-red: #ec1f27;
    --icon-orange: #ef4a2a;
    --ink: #2b2b2b;
    --body-ink: #3a3a3a;
    --swoosh-grey: #e8e8e8;
    --swoosh-peach: #fbdcd2;
    --paper: #ffffff;
  }
  html, body {
    margin: 0;
    padding: 0;
    width: 889px;
    height: 1200px;
    overflow: hidden;
    background: var(--paper);
  }
  .letterhead {
    position: relative;
    width: 889px;
    height: 1200px;
    background: var(--paper);
    font-family: "Montserrat", sans-serif;
    color: var(--ink);
    overflow: hidden;
  }
  .swooshes {
    position: absolute;
    inset: 0;
    width: 889px;
    height: 1200px;
  }
  .swoosh-grey { fill: var(--swoosh-grey); }
  .swoosh-peach { fill: var(--swoosh-peach); }

  .brand-name {
    position: absolute;
    left: 63px;
    top: 50px;
    margin: 0;
    color: var(--brand-red);
    font-weight: 800;
    text-transform: uppercase;
    line-height: 1;
  }
  .brand-name .brand-primary { display: block; font-size: 42px; letter-spacing: 1px; }
  .brand-name .brand-secondary { display: block; font-size: 19px; letter-spacing: 2px; margin-top: 10px; }

  .contact-list {
    position: absolute;
    right: 68px;
    top: 76px;
    margin: 0;
    padding: 0;
    list-style: none;
    text-align: right;
    font-weight: 700;
    font-size: 15px;
  }
  .contact-list li {
    display: flex;
    justify-content: flex-end;
    align-items: center;
    gap: 8px;
    height: 20px;
  }
  .contact-icon { width: 17px; height: 17px; flex: none; }
  .contact-icon circle { fill: none; stroke: var(--icon-orange); stroke-width: 1.3; }
  .contact-icon .glyph { fill: var(--icon-orange); }
  .contact-icon .glyph-line { fill: none; stroke: var(--icon-orange); stroke-width: 1; }

  .header-rule {
    position: absolute;
    left: 63px;
    top: 164px;
    width: 758px;
    height: 2px;
    background: var(--brand-red);
  }

  .signoff {
    position: absolute;
    left: 63px;
    top: 240px;
  }
  .signoff .closing { margin: 0; font-size: 13px; }
  .signoff .signer-name { margin: 14px 0 0; font-size: 23px; font-weight: 700; letter-spacing: 0.5px; line-height: 1; }
  .signoff .signer-title { margin: 4px 0 0; font-size: 15px; font-weight: 700; }

  .letter-body {
    position: absolute;
    left: 63px;
    width: 760px;
    margin: 0;
    font-size: 13px;
    line-height: 28px;
    color: var(--body-ink);
  }
  .letter-body.first { top: 474px; }
  .letter-body.second { top: 656px; }
  .letter-body.third { top: 796px; }

  .footer-rule {
    position: absolute;
    left: 0;
    top: 1108px;
    width: 889px;
    height: 2px;
    background: var(--brand-red);
  }
  .footer-address,
  .footer-license {
    position: absolute;
    top: 1126px;
    margin: 0;
    font-size: 17px;
    font-weight: 700;
  }
  .footer-address { left: 63px; color: var(--ink); }
  .footer-license { right: 68px; color: var(--brand-red); }
</style>
</head>
<body>
<main class="letterhead">
  <svg class="swooshes" viewBox="0 0 889 1200" aria-hidden="true">
    <path class="swoosh-grey" d="M0,269 Q450,250 765,0 L849,0 Q520,270 0,281 Z"/>
    <path class="swoosh-grey" d="M524,214 Q730,165 889,28 L889,77 Q730,180 524,214 Z"/>
    <path class="swoosh-peach" d="M201,1200 Q330,1135 522,1103 Q380,1150 282,1200 Z"/>
    <path class="swoosh-peach" d="M522,1200 Q680,1125 889,1100 L889,1116 Q710,1150 602,1200 Z"/>
  </svg>

  <h1 class="brand-name">
    <span class="brand-primary">Dorwin's</span>
    <span class="brand-secondary">Coating &amp; Renewal</span>
  </h1>

  <ul class="contact-list">
    <li>(555) 413-2986
      <svg class="contact-icon" viewBox="0 0 17 17" aria-hidden="true">
        <circle cx="8.5" cy="8.5" r="7.5"/>
        <path class="glyph" d="M5.6,4.6 L7,4.4 L7.7,6.4 L6.8,7.1 Q7.6,8.9 9.6,10 L10.4,9.1 L12.3,9.9 L12.1,11.3 Q8.3,11.6 5.4,7.2 Q5.1,5.7 5.6,4.6 Z"/>
      </svg>
    </li>
    <li>Dorwinrenewal@mailbrook.example
      <svg class="contact-icon" viewBox="0 0 17 17" aria-hidden="true">
        <circle cx="8.5" cy="8.5" r="7.5"/>
        <rect class="glyph" x="5" y="6" width="7" height="5" rx="0.6"/>
        <path d="M5.2,6.3 L8.5,8.8 L11.8,6.3" fill="none" stroke="#fff" stroke-width="0.8"/>
      </svg>
    </li>
    <li>www.dorwinrenewal.example
      <svg class="contact-icon" viewBox="0 0 17 17" aria-hidden="true">
        <circle cx="8.5" cy="8.5" r="7.5"/>
        <circle cx="8.5" cy="8.5" r="3.8" class="glyph-line" style="stroke-width:1"/>
        <ellipse class="glyph-line" cx="8.5" cy="8.5" rx="1.6" ry="3.8"/>
        <path class="glyph-line" d="M4.7,8.5 H12.3"/>
      </svg>
    </li>
  </ul>

  <div class="header-rule"></div>

  <section class="signoff">
    <p class="closing">Sincearly,</p>
    <p class="signer-name">MARLA BENNING</p>
    <p class="signer-title">Director</p>
  </section>

  <p class="letter-body first">This is a sample letter that has been placed to demonstrate typing remat (Your Company).letterhead design. When positioned properly, it will serve to work in harmony with all other elements letterhead. This letterhead design is meant to project an image&nbsp; This letterhead design is meant project an image of professionalism reliability. By using simple aligen we have created a very spacious feeling. The simplicity suggest&nbsp; rengththe spaciousnes contributes haesthetics the layout. These basic qualities along with the (Your Company)</p>

  <p class="letter-body second">look and helps reinforce the (Your Company) brand. letterhead design is meant to project an image design. When positioned properly, it will serve to work in harmony all the other elements letterhead. sionalism and reliability.</p>

  <p class="letter-body third">This letterhead design is based on the (Form of your logo) form (Your Company) logo. Each stationery we have created a very spacious feeling. The simplicity suggests strength the spaciousnes contribute part of the (Form of your logo). This letterhead design is based on the (Form of your logo) form (Your Company) logo. Each stationery we have created a very spacious feeling. The simplicity suggests strength the spaciousnes contribute part of the (Form of your logo).</p>

  <div class="footer-rule"></div>
  <p class="footer-address">4728 SW 81st Ter . Halverd Cove, Florida 39417</p>
  <p class="footer-license">KRT8046392</p>
</main>
</body>
</html>
```